Outdoor Banners for Shopping Center

I need outdoor banners for a small California Shopping Center (Calloway Pines Plaza). You must include the property logo. Each parking lot pole will have 2 banners -- one on each side of the pole so the design should take that into account. Use bright colors… something that will work well with the logo. Size for each banner is 30"w x 96"h. It should be bold and easy to read (if you include any additional text).

Target Market(s)

Middle class shoppers.

Industry/Entity Type

Graphic Design

Font styles to use
Serif
Sans Serif

Requirements
Must have
• The property logo.

```html
<!DOCTYPE html>
<html lang="en">
<head>
<meta charset="utf-8">
<title>Calloway Pines Plaza – Pole Banners</title>
<link rel="stylesheet" href="https://fonts.googleapis.com/css2?family=Roboto+Condensed:wght@700&display=swap">
<style>
  :root {
    --page: #ffffff;
    --sun-yellow: #fff200;
    --hot-magenta: #ff00ff;
    --ink-black: #111111;
    --ink-white: #ffffff;
    --brand-navy: #1b2a7a;
    --burst-pink: #ff2fc8;
    --burst-violet: #7b4ff0;
    --burst-blue: #4a5cf0;
    --burst-lime: #a6f03a;
    --burst-orange: #ffa21a;
    --burst-cream: #fff0b8;
  }
  * { box-sizing: border-box; margin: 0; padding: 0; }
  html, body {
    width: 848px; height: 1200px; overflow: hidden;
    background: var(--page);
  }
  .canvas {
    position: relative; width: 848px; height: 1200px;
    font-family: "Roboto Condensed", "Arial Narrow", sans-serif;
  }
  .banner {
    position: absolute; top: 83px;
    width: 322px; height: 1034px;
    overflow: hidden;
  }
  .banner--yellow { left: 77px; background: var(--sun-yellow); }
  .banner--magenta { left: 457px; background: var(--hot-magenta); }

  .brand-name {
    position: absolute; left: 0; width: 100%;
    text-align: center;
    font-weight: 700; font-size: 36px; line-height: 1.05;
    color: var(--brand-navy);
    text-transform: uppercase;
  }
  .banner--yellow .brand-name { top: 86px; }
  .banner--magenta .brand-name { top: 872px; }

  .burst {
    position: absolute; left: 8px; width: 306px;
    border-radius: 46% 54% 42% 58% / 38% 44% 56% 62%;
  }
  .banner--yellow .burst {
    top: 257px; height: 513px;
    background: linear-gradient(155deg,
      var(--burst-pink) 0%, var(--burst-violet) 30%,
      var(--burst-blue) 45%, var(--burst-lime) 62%,
      var(--burst-pink) 85%);
  }
  .banner--magenta .burst {
    top: 257px; height: 475px;
    background: linear-gradient(155deg,
      var(--burst-cream) 0%, var(--burst-orange) 28%,
      var(--burst-violet) 45%, var(--burst-lime) 62%,
      var(--burst-orange) 82%, var(--burst-cream) 100%);
  }

  .tagline {
    position: absolute; left: 0; width: 100%;
    text-align: center;
    font-weight: 700; font-size: 62px; line-height: 0.98;
    letter-spacing: -0.5px;
  }
  .banner--yellow .tagline { top: 804px; color: var(--ink-black); }
  .banner--magenta .tagline { top: 36px; color: var(--ink-white); }
</style>
</head>
<body>
<main class="canvas">
  <section class="banner banner--yellow" aria-label="Banner, yellow side">
    <p class="brand-name">Calloway Pines<br>Plaza</p>
    <div class="burst" role="img" aria-label="Colourful splash burst of pink, violet, blue and lime droplet shapes"></div>
    <h2 class="tagline">A Great<br>Place<br>to Be!</h2>
  </section>

  <section class="banner banner--magenta" aria-label="Banner, magenta side">
    <h2 class="tagline">A Great<br>Place<br>to Be!</h2>
    <div class="burst" role="img" aria-label="Colourful splash burst of orange, cream, violet and lime droplet shapes"></div>
    <p class="brand-name">Calloway Pines<br>Plaza</p>
  </section>
</main>
</body>
</html>
```